My name is Delia Okonkwo,I want to create a web page for my personal dog grooming business. The name on the web page can be "Delia's Dog Grooming" I am located in San Antonio Texas. The page would help grow my customer base. Before and after pictures would display the quality of work that I do. On my page I can provide information about myself, my services, and pricing.
Updates

I have updated project to guaranteed pay

Please try to incorporate a schnauzer in an icon or logo. My dog is a schnauzer. THANKS!!!!!!!!!!!!

Target Market(s)

Dog Owners

Industry/Entity Type

Business

Requirements
Must have
• -A spot for before and after pictures.
-An about me section
-A section to make an appointment
Nice to have
• My favorite Color is purple. I think different shades of purple would be nice or purple with a light green

please incorporate a schnauzer in any icon or logo. My dog is a schnauzer.

```html
<!DOCTYPE html>
<html lang="en">
<head>
<meta charset="utf-8">
<title>Delia's Dog Grooming</title>
<link href="https://fonts.googleapis.com/css2?family=Roboto+Condensed:wght@400;700&family=Open+Sans:wght@400&display=swap" rel="stylesheet">
<style>
  :root {
    --plum: #7a0f60;
    --plum-dark: #6e0757;
    --nav: #800a66;
    --nav-line: #93287a;
    --mauve-text: #b39aab;
    --grey-text: #9a9a9a;
    --dark-text: #2a2a2a;
    --hero-bg: #f3f0f3;
    --band-bg: #f2f2f2;
    --rule: #3a3a3a;
    --button: #d7c5d1;
    --white: #ffffff;
  }
  * { box-sizing: border-box; margin: 0; padding: 0; }
  html, body { width: 1167px; height: 1200px; overflow: hidden; background: var(--white); }
  body { position: relative; font-family: "Open Sans", Verdana, sans-serif; }
  .abs { position: absolute; }
  .heading { font-family: "Roboto Condensed", "Arial Narrow", sans-serif; font-weight: 400; color: var(--plum); text-transform: uppercase; }

  /* header */
  .site-header { left: 0; top: 0; width: 1167px; height: 119px;
    background: linear-gradient(90deg, #f1e6ef 0%, #fbf8fa 45%, #ffffff 62%, #eadbe6 100%); }
  .brand { left: 40px; top: 26px; font-family: "Roboto Condensed", sans-serif; font-weight: 700;
    font-size: 54px; color: var(--plum-dark); letter-spacing: 0.5px; white-space: nowrap; }

  /* navigation */
  .main-nav { left: 0; top: 119px; width: 1167px; height: 55px; background: var(--nav);
    display: flex; overflow: hidden; }
  .main-nav a { font-family: "Roboto Condensed", sans-serif; font-size: 18.5px; color: var(--white);
    text-decoration: none; line-height: 55px; text-align: center; border-right: 1px solid var(--nav-line);
    white-space: nowrap; flex: none; }
  .main-nav a:first-child { text-align: left; padding-left: 35px; }
  .main-nav a:last-child { border-right: none; }

  /* hero */
  .hero { left: 0; top: 174px; width: 1167px; height: 414px; background: var(--hero-bg); }
  .hero-photo { left: 58px; top: 0; width: 612px; height: 403px;
    background: radial-gradient(ellipse at 50% 55%, #6b6266 0%, #a39a9c 45%, rgba(243,240,243,0) 72%); }
  .hero-arrow { top: 140px; }
  .hero-title { left: 708px; top: 103px; font-size: 56px; line-height: 1; }
  .hero-text { left: 708px; top: 178px; width: 345px; font-size: 20px; line-height: 29px;
    letter-spacing: 0.6px; color: var(--mauve-text); }
  .hero-rule { left: 0; top: 588px; width: 1167px; height: 1px; background: var(--rule); }

  /* columns */
  .col-heading { top: 623px; font-size: 27px; line-height: 1; }
  .welcome-photo { left: 42px; top: 667px; width: 309px; height: 104px; border: 1px solid #d8d8d8;
    background: linear-gradient(180deg, #f4f2f3 0%, #8c8487 60%, #5d5659 100%); }
  .welcome-text { left: 44px; top: 776px; width: 306px; font-size: 13px; line-height: 19.5px;
    color: var(--grey-text); text-align: justify; }
  .news-list { left: 411px; top: 676px; width: 352px; list-style: none; }
  .news-list li { margin-bottom: 19px; }
  .news-date { font-size: 13px; color: var(--plum); line-height: 20px; }
  .news-text { font-size: 13px; color: var(--grey-text); line-height: 20px; }
  .article-list { left: 805px; top: 676px; width: 350px; list-style: none; }
  .article-list li { margin-bottom: 19px; line-height: 13.5px; }
  .article-list li:nth-child(3) { margin-top: 33px; margin-bottom: 25px; padding-left: 4px; }
  .article-list li:nth-child(4) { padding-left: 9px; }
  .article-title { font-size: 13.5px; color: var(--plum); }
  .article-meta { font-size: 13.5px; color: #777; }

  /* lower band */
  .lower-band { left: 0; top: 927px; width: 1167px; height: 201px; background: var(--band-bg);
    border-bottom: 4px solid #e4e4e4; }
  .band-heading { top: 956px; font-size: 23.5px; line-height: 1; }
  .form-label { font-size: 13.5px; color: #333; }
  .form-field { height: 29px; background: var(--white); border: 1px solid #bdbdbd; }
  .submit-btn { left: 478px; top: 1086px; width: 78px; height: 23px; background: var(--button);
    border: none; border-radius: 5px; font-family: "Roboto Condensed", sans-serif; font-size: 12.5px;
    color: var(--plum); text-transform: uppercase; }
  .result-photo { top: 988px; height: 97px; border: 1px solid #cfcfcf; }
  .result-photo.before { left: 591px; width: 126px;
    background: linear-gradient(160deg, #6f8a52 0%, #9a9894 45%, #5c5659 100%); }
  .result-photo.after { left: 725px; width: 127px;
    background: linear-gradient(160deg, #b5aea4 0%, #4c4446 55%, #2e2a2b 100%); }
  .result-label { top: 1090px; font-family: "Roboto Condensed", sans-serif; font-size: 13px; color: #555; width: 126px; text-align: center; }
  .testimonial-text { left: 884px; top: 989px; width: 249px; font-size: 13px; line-height: 17px;
    color: var(--dark-text); text-align: justify; }

  /* footer */
  .copyright { left: 30px; top: 1157px; font-size: 11px; color: #333; }
  .social { left: 1044px; top: 1154px; display: flex; gap: 8px; }
  .social-square { width: 18px; height: 18px; border-radius: 2px; }
</style>
</head>
<body>

  <header class="abs site-header">
    <div class="abs brand">DELIA'S DOG GROOMING</div>
  </header>

  <nav class="abs main-nav">
    <a href="#" style="width:127px">ABOUT US</a>
    <a href="#" style="width:126px">DOG BREEDS</a>
    <a href="#" style="width:101px">ARTICLES</a>
    <a href="#" style="width:176px">BRINGING UP A PET</a>
    <a href="#" style="width:84px">VIDEOS</a>
    <a href="#" style="width:163px">PICTURE GALLERY</a>
    <a href="#" style="width:142px">NEWSLETTERS</a>
    <a href="#" style="width:125px">CONTACT US</a>
    <a href="#" style="width:123px">ADOPTION</a>
  </nav>

  <section class="abs hero">
    <div class="abs hero-photo" role="img" aria-label="Photo of a schnauzer lying down"></div>
    <svg class="abs hero-arrow" style="left:18px" width="52" height="100" viewBox="0 0 52 100" aria-hidden="true">
      <polygon points="50,2 2,50 50,98 50,80 20,50 50,20" fill="#e3dee2"/>
    </svg>
    <svg class="abs hero-arrow" style="left:1097px" width="52" height="100" viewBox="0 0 52 100" aria-hidden="true">
      <polygon points="2,2 50,50 2,98 2,80 32,50 2,20" fill="#e3dee2"/>
    </svg>
    <h1 class="abs heading hero-title">VET SUPPORT</h1>
    <p class="abs hero-text">Dog grooming refers to both the hygienic care and cleaning of a dog</p>
  </section>
  <div class="abs hero-rule"></div>

  <h2 class="abs heading col-heading" style="left:44px">WELCOME</h2>
  <div class="abs welcome-photo" role="img" aria-label="Photo of a schnauzer sitting"></div>
  <p class="abs welcome-text">Dog grooming refers to both the hygienic care and cleaning of a dog, as well as a process by which a dog's physical appearance is enhanced for showing or other types of competition. A dog groomer (or simply "groomer") is a person who earns their living grooming dogs</p>

  <h2 class="abs heading col-heading" style="left:409px">LATEST&nbsp; NEWS</h2>
  <ul class="abs news-list">
    <li><div class="news-date">1.12.11</div><div class="news-text">other types of competition. A dog groomer is a person who earns their living grooming dogs</div></li>
    <li><div class="news-date">1.12.11</div><div class="news-text">other types of competition. A dog groomer is a person who earns their living grooming dogs</div></li>
    <li><div class="news-date">1.12.11</div><div class="news-text">other types of competition. A dog groomer is a person who earns their living grooming dogs</div></li>
  </ul>

  <h2 class="abs heading col-heading" style="left:812px">ARICLES</h2>
  <ul class="abs article-list">
    <li><div class="article-title">Easy Tricks To Teach Your Dog</div><div class="article-meta">Source : Admin Date : August 18, 2011, 1:25 am</div></li>
    <li><div class="article-title">Easy Tricks To Teach Your Dog</div><div class="article-meta">Source : Admin Date : August 18, 2011, 1:25 am</div></li>
    <li><div class="article-title">Easy Tricks To Teach Your Dog</div><div class="article-meta">Source : Admin Date : August 18, 2011, 1:25 am</div></li>
    <li><div class="article-title">Easy Tricks To Teach Your Dog</div><div class="article-meta">Source : Admin Date : August 18, 2011, 1:25 am</div></li>
  </ul>

  <section class="abs lower-band"></section>

  <h2 class="abs heading band-heading" style="left:23px">ONLINE APPOINTMENT</h2>
  <span class="abs form-label" style="left:29px;top:996px">Name:</span>
  <div class="abs form-field" style="left:77px;top:992px;width:199px"></div>
  <span class="abs form-label" style="left:306px;top:996px">Date:</span>
  <div class="abs form-field" style="left:354px;top:990px;width:199px"></div>
  <span class="abs form-label" style="left:29px;top:1044px">Phone:</span>
  <div class="abs form-field" style="left:79px;top:1038px;width:199px"></div>
  <span class="abs form-label" style="left:285px;top:1044px">Timeing:</span>
  <div class="abs form-field" style="left:354px;top:1041px;width:199px"></div>
  <button class="abs submit-btn">Submit</button>

  <h2 class="abs heading band-heading" style="left:591px">RESULTS</h2>
  <div class="abs result-photo before" role="img" aria-label="Before photo of a schnauzer prior to grooming"></div>
  <div class="abs result-photo after" role="img" aria-label="After photo of a freshly groomed schnauzer"></div>
  <span class="abs result-label" style="left:591px">BEFOUR</span>
  <span class="abs result-label" style="left:725px">AFTER</span>

  <h2 class="abs heading band-heading" style="left:884px">TESTIMONIALS</h2>
  <p class="abs testimonial-text">Dog grooming refers to both the hygienic care and cleaning of a dog, as well as a process by which a dog's physical appearance is enhanced for showing or other types of competition.</p>

  <footer>
    <p class="abs copyright">All Copyright 2012 Delia's Dog Grooming</p>
    <div class="abs social">
      <span class="social-square" style="background:#3b5a98"></span>
      <span class="social-square" style="background:#4fb3e3"></span>
      <svg width="20" height="18" viewBox="0 0 20 18" aria-label="Email">
        <rect x="1" y="3" width="18" height="12" fill="none" stroke="#333" stroke-width="1.3"/>
        <polyline points="1,3 10,10 19,3" fill="none" stroke="#333" stroke-width="1.3"/>
      </svg>
    </div>
  </footer>

</body>
</html>
```